CBD AgriBusiness Verdant Trophy Business Card

We are HiTec producer of medical cannabis CBD Switzerland of high quality. Our website is alpinleaf.net, we will also revisit it graphically, the winner of this contest will be the graphic designer chosen for the new design of the website. We stand out by the skill of the team, many of our engineers we win cup cannabis. I join the current map to take as an example but to revisit completely: deletion of surname and first name, modification of funds (front / back), reorganization of text info, highlighting the address of the website. three characteristics define the business card: Professional, Class, refined. The business card must be optimized for soft-touch and selective varnish printing.

Target Market(s)

Customers and Suppliers

Industry/Entity Type

Agribusiness

Contact Information for Business Card

Logo, Tél / Whatsapp, mail, url du site : alpinleaf.net

Font styles to use
Sans Serif

Requirements
Must have
• Logo of alpinleaf.net
Nice to have
• a design that stands out well on the selective varnish
Should not have
• Last name and first name

```html
<!DOCTYPE html>
<html lang="en">
<head>
<meta charset="utf-8">
<title>alpinleaf business card</title>
<link href="https://fonts.googleapis.com/css2?family=Work+Sans:wght@400;500;700&display=swap" rel="stylesheet">
<style>
  :root {
    --bg: #b9b9b9;
    --card-dark: #58585b;
    --card-light: #ffffff;
    --green: #7cc04b;
    --ink: #555558;
    --ink-soft: #6a6a6d;
  }
  * { margin: 0; padding: 0; box-sizing: border-box; }
  html, body { width: 1200px; height: 930px; overflow: hidden; }
  body {
    background: var(--bg);
    font-family: "Work Sans", Arial, sans-serif;
    display: flex;
    flex-direction: column;
    align-items: center;
    justify-content: center;
    gap: 60px;
  }
  .card {
    width: 560px;
    height: 320px;
    border-radius: 18px;
    position: relative;
    overflow: hidden;
  }
  .card--back { background: var(--card-dark); }
  .card--front { background: var(--card-light); }

  .brand {
    position: absolute;
    display: flex;
    align-items: center;
    gap: 12px;
  }
  .brand__mark {
    width: 30px; height: 30px;
    background: var(--green);
  }
  .brand__name {
    font-weight: 700;
    font-size: 56px;
    letter-spacing: -1px;
    line-height: 1;
  }
  .card--back .brand { left: 50%; top: 50%; transform: translate(-50%, -50%); }
  .card--back .brand__name { color: #ffffff; }
  .card--front .brand { left: 40px; top: 190px; }
  .card--front .brand__name { color: var(--ink); font-size: 44px; }
  .card--front .brand__mark { width: 24px; height: 24px; }

  .divider {
    position: absolute;
    left: 300px; top: 60px;
    width: 2px; height: 200px;
    background: var(--green);
  }
  .contact {
    position: absolute;
    left: 322px; top: 84px;
    color: var(--ink-soft);
    font-size: 13px;
    line-height: 1.45;
  }
  .contact__role {
    color: var(--green);
    font-weight: 500;
    font-size: 13px;
    margin-bottom: 12px;
  }
  .contact__address { margin-bottom: 12px; }
  .contact__list { list-style: none; }
  .contact__list li { display: flex; align-items: center; gap: 8px; }
  .contact__list svg { width: 10px; height: 10px; flex: none; }
  .contact__web-domain { color: var(--green); }
</style>
</head>
<body>
  <section class="card card--back" aria-label="Card back">
    <div class="brand">
      <span class="brand__mark"></span>
      <span class="brand__name">alpinleaf</span>
    </div>
  </section>

  <section class="card card--front" aria-label="Card front">
    <div class="brand">
      <span class="brand__mark"></span>
      <span class="brand__name">alpinleaf</span>
    </div>
    <div class="divider"></div>
    <div class="contact">
      <p class="contact__role">Director</p>
      <p class="contact__address">12 Birch Lane,<br>Ashford, 4020</p>
      <ul class="contact__list">
        <li>
          <svg viewBox="0 0 10 10" aria-hidden="true"><path d="M2 1 L4 3 L3 4 Q4 6 6 7 L7 6 L9 8 L8 9 Q4 9 1 5 Q1 2 2 1Z" fill="#7cc04b"/></svg>
          +41 (0) 70 555 01 23
        </li>
        <li>
          <svg viewBox="0 0 10 10" aria-hidden="true"><rect x="2.5" y="0.5" width="5" height="9" rx="1" fill="none" stroke="#7cc04b"/><circle cx="5" cy="8" r="0.6" fill="#7cc04b"/></svg>
          +44 7700 90 01 45
        </li>
        <li>
          <svg viewBox="0 0 10 10" aria-hidden="true"><rect x="0.5" y="2" width="9" height="6.5" fill="none" stroke="#7cc04b"/><path d="M0.5 2 L5 6 L9.5 2" fill="none" stroke="#7cc04b"/></svg>
          office@alpinleaf.net
        </li>
        <li>
          <svg viewBox="0 0 10 10" aria-hidden="true"><circle cx="5" cy="5" r="4.5" fill="#7cc04b"/><path d="M0.5 5 H9.5 M5 0.5 Q2 5 5 9.5 Q8 5 5 0.5" fill="none" stroke="#fff" stroke-width="0.7"/></svg>
          <span>www.<span class="contact__web-domain">alpinleaf</span>.net</span>
        </li>
      </ul>
    </div>
  </section>
</body>
</html>
```